Creative, fresh business card design for Ripplecraft Facades

We need a fresh, creative business card design for Ripplecraft Facades. We are the manufacturer of Ripplecraft Facades in Australia. Wall panels are 2400 x 1200mm panels made from MDF and feature 3D patterns on the face of the panel. The colours to be used are green, silver/grey and white RGB
Red 187
Green 207
Blue 65.

An idea is to possibly use a watermark of one of our designs as a background (like on the "Grids" design on the left hand side of page 2 of our brochure).

Target Market(s)

Interior designers, architects, builders and home renovators

Industry/Entity Type

Business

Contact Information for Business Card

Details to go on the card are:
Our logo (attached),
Slogan: "Decorative panels for interiors and exteriors",
Contact name,
Position,
Mobile phone number,
Business address,
Business phone,
Business fax,
Website and
Email address.

I have attached a few images of our panels and our brochure for reference.

The colours of the business card should feature our logo colours which are: RGB
Red 187
Green 207
Blue 65

Requirements
Must have
• Very modern fonts and design. Some of the designs shown especially the "Prisms" design which is a popular design.
Nice to have
• Creative but simple design. Very contemporary.
Should not have
• Anything ornate or old fashioned.

```html
<!DOCTYPE html>
<html lang="en">
<head>
<meta charset="utf-8">
<title>Ripplecraft Facades – Business Card</title>
<link href="https://fonts.googleapis.com/css2?family=Open+Sans:wght@400;600;700&display=swap" rel="stylesheet">
<style>
  :root{
    --brand-green:#bbcf41;
    --card-white:#ffffff;
    --ink:#1d1d1b;
    --silver:#8e8f93;
    --silver-light:#a9aaad;
    --prism-light:#f3f3f4;
    --prism-mid:#e3e4e6;
    --stage:#ecedef;
  }
  *{margin:0;padding:0;box-sizing:border-box}
  html,body{width:1200px;height:900px;overflow:hidden}
  body{background:var(--stage);font-family:"Open Sans",Arial,sans-serif;position:relative;color:var(--ink)}

  .card{position:absolute;background:var(--card-white);overflow:hidden;box-shadow:0 4px 14px rgba(0,0,0,.12)}
  .card--front{left:77px;top:35px;width:588px;height:363px}
  .card--back{left:388px;top:505px;width:567px;height:352px}

  /* front */
  .contact-panel{position:absolute;left:0;top:0;width:278px;height:100%;background:var(--brand-green);padding:58px 0 0 31px}
  .contact-name{font-size:20px;font-weight:700;line-height:24px}
  .contact-role{font-size:15px;line-height:20px}
  .contact-address{margin-top:24px;font-size:15px;line-height:18px}
  .contact-list{list-style:none;margin-top:25px}
  .contact-list li{display:flex;align-items:center;font-size:15px;height:24.5px}
  .contact-list svg{width:12px;height:12px;margin-right:11px;flex:none}

  .prism-texture{position:absolute}
  .card--front .prism-texture{right:0;top:0;width:310px;height:100%;
    background:radial-gradient(ellipse at 85% 40%,var(--prism-mid),var(--prism-light) 45%,rgba(255,255,255,0) 75%)}

  .brand-lockup{position:absolute;display:flex;align-items:center;gap:14px}
  .brand-mark{width:40px;height:40px;background:var(--brand-green);flex:none}
  .brand-name{font-size:26px;font-weight:600;line-height:30px;color:var(--silver)}
  .card--front .brand-lockup{left:318px;top:130px}

  .slogan{position:absolute;left:318px;top:232px;width:222px;font-size:12.5px;letter-spacing:2.1px;line-height:17px;color:var(--silver-light);text-align:center}

  /* back */
  .card--back .prism-texture--top{left:0;top:0;width:230px;height:106px;
    background:linear-gradient(90deg,var(--prism-mid),rgba(255,255,255,0))}
  .card--back .prism-texture--bottom{left:0;top:250px;width:230px;height:102px;
    background:linear-gradient(90deg,var(--prism-mid),rgba(255,255,255,0))}
  .band{position:absolute;top:106px;height:144px;background:var(--brand-green)}
  .band--left{left:0;width:148px}
  .band--right{left:425px;width:142px}
  .card--back .brand-lockup{left:164px;top:144px}
</style>
</head>
<body>

<section class="card card--front">
  <div class="contact-panel">
    <p class="contact-name">Marcus Hale</p>
    <p class="contact-role">Managing Director</p>
    <p class="contact-address">12345, Address Goes Here<br>Country Name, 123456</p>
    <ul class="contact-list">
      <li><svg viewBox="0 0 12 12"><rect x="2.5" y="0.5" width="7" height="11" rx="1.2" fill="none" stroke="#1d1d1b" stroke-width="1.4"/><rect x="4" y="2" width="4" height="6.5" fill="#1d1d1b"/></svg>123-456-7890</li>
      <li><svg viewBox="0 0 12 12"><path d="M2.2 0.8l2 2.2-1 1.4c.7 1.7 2 3 3.7 3.7l1.4-1 2.2 2-1 2C5.6 11 1 6.4.8 1.8z" fill="#1d1d1b"/></svg>(044)-456-7890</li>
      <li><svg viewBox="0 0 12 12"><rect x="1" y="4" width="10" height="7" rx="1" fill="#1d1d1b"/><rect x="3" y="1" width="6" height="4" fill="none" stroke="#1d1d1b" stroke-width="1.2"/><rect x="3" y="6" width="6" height="1" fill="#bbcf41"/><rect x="3" y="8" width="6" height="1" fill="#bbcf41"/></svg>123-456-7890</li>
      <li><svg viewBox="0 0 12 12"><rect x="0.5" y="2.5" width="11" height="7.5" fill="#1d1d1b"/><path d="M1 3l5 4 5-4" fill="none" stroke="#bbcf41" stroke-width="1"/></svg>info@youremail.com</li>
      <li><svg viewBox="0 0 12 12"><circle cx="6" cy="6" r="5.5" fill="#1d1d1b"/><path d="M0.8 6h10.4M6 .5v11M2.5 3h7M2.5 9h7" stroke="#bbcf41" stroke-width=".7" fill="none"/></svg>www.website.com</li>
    </ul>
  </div>

  <div class="prism-texture" role="img" aria-label="Faint white prism wall panel pattern"></div>

  <div class="brand-lockup">
    <span class="brand-mark"></span>
    <span class="brand-name">Ripplecraft<br>Facades</span>
  </div>
  <p class="slogan">decorative panels for interiors &amp; landscapes</p>
</section>

<section class="card card--back">
  <div class="prism-texture prism-texture--top" role="img" aria-label="Faint white prism wall panel pattern"></div>
  <div class="prism-texture prism-texture--bottom" role="img" aria-label="Faint white prism wall panel pattern"></div>
  <div class="band band--left"></div>
  <div class="band band--right"></div>
  <div class="brand-lockup">
    <span class="brand-mark"></span>
    <span class="brand-name">Ripplecraft<br>Facades</span>
  </div>
</section>

</body>
</html>
```